"Inkvale" printing shop

-The design must be based around the attached HPID (home page information design) called "Inkvale - HPID".

The table boxes are just for approximate placement of information – you DON'T have to box everything in and you can arrange these. All fonts used in the HPID are only examples - you can use any Google font you wish.

- Information only is in orange text. Copy to go on the design in black text. Some instructions are in the HPID. Please be creative!

-The design needs to be modern. Colours are to be consistent with their new logo or complement it. Keep it clean and simple, you don't need to use lots of colours. Use lots of white.

- images / icons for the site need to be relevant and high quality, but they must also be free images or icons. I have attached a few examples that could be used.

Width of content will be 1100 pixels when implemented as a web page. Header height (without nav bar) 150-200 pixels.

If your design is chosen the winning PSD file will have to be provided as follows…
1. Canvas size of 2000px x 2000px - 72ppi in Adobe Photoshop (CS5 compatible)
2. Width of content section is 1100px wide - centered in the canvas
3. Any button rollovers/hovers in the PSD as hidden layers.
4. All fonts used must be Google fonts.
5. You will need to supply the chosen home page plus one example page (example page as a style guide for how all other pages will look). Example page is only the header and navigational bar at the top, an empty sector in the middle with a column (190 px wide) which can be left or right aligned which means the main sector is 910 pixels wide, and then the footer at the bottom of the page

Checklist - http://pagebuildertally.example/

Examples of some websites that have great design... don't copy them please but they are similar in look to what we are after....
http://www.rookfenly.example/

Industry/Entity Type

Printing

Font styles to use
Serif
Sans Serif

Requirements
Should not have
• Drop shadows, comic sans font

```html
<!DOCTYPE html>
<html lang="en">
<head>
<meta charset="utf-8">
<title>Inkvale – Printing &amp; Photocopying</title>
<link href="https://fonts.googleapis.com/css2?family=Ubuntu:wght@300;400;500;700&display=swap" rel="stylesheet">
<style>
:root{
  --navy:#22237a;
  --navy-deep:#1a1b5e;
  --magenta:#d23bb4;
  --ink:#333;
  --muted:#777;
  --panel:#f4f4f6;
  --line:#e3e3e3;
  --blue:#1e8fd8;--pink:#d81b72;--red:#d71f2b;--plum:#9c2f86;--yellow:#fbbe14;--green:#1f9a3e;
}
*{margin:0;padding:0;box-sizing:border-box}
html,body{width:746px;height:1200px;overflow:hidden;background:#fff}
body{font-family:'Ubuntu',sans-serif;color:var(--ink);position:relative}
.abs{position:absolute}

/* header */
.brand{left:100px;top:22px;display:flex;align-items:center;gap:8px}
.brand-dot{width:40px;height:40px;border-radius:50%;background:var(--navy)}
.brand-name{font-size:30px;font-weight:500;color:var(--navy);letter-spacing:-.5px}
.tagline{left:270px;top:24px}
.tagline strong{display:block;font-size:8.5px;font-weight:500;color:var(--navy)}
.tagline span{display:block;font-size:6.5px;color:#555;margin-top:4px}
.contact{left:512px;top:21px;font-size:6.5px;color:#555}
.contact strong{display:block;font-size:8.5px;color:var(--navy);font-weight:500;margin-bottom:3px}

.util-bar{left:252px;top:62px;width:494px;height:24px;
  background:linear-gradient(90deg,#1fa36a 0%,#2b8fcf 22%,#6b72e6 48%,#b04bd8 72%,#ee3a8a 90%,#f2463f 100%);
  clip-path:polygon(14px 0,100% 0,100% 100%,0 100%)}
.util-bar a{position:absolute;top:8px;font-size:6.8px;color:#fff;text-decoration:none;text-transform:uppercase}
.util-bar .sep{position:absolute;top:0;width:1px;height:24px;background:rgba(255,255,255,.25)}

.main-nav{left:0;top:86px;width:746px;height:27px;background:linear-gradient(180deg,#2a2b86,var(--navy-deep))}
.main-nav a{position:absolute;top:0;height:27px;line-height:27px;font-size:6.8px;color:#fff;text-decoration:none;text-transform:uppercase}
.main-nav a.active{background:var(--magenta);padding:0 10px}
.main-nav .sep{position:absolute;top:0;width:1px;height:27px;background:rgba(255,255,255,.12)}

/* hero */
.hero{left:0;top:113px;width:746px;height:280px;
  background:
   radial-gradient(ellipse at 25% 60%,rgba(40,60,200,.85),transparent 55%),
   linear-gradient(100deg,#0f8a6a 0%,#1a3c8c 25%,#3b2ab8 45%,#8a2ab0 62%,#d2303c 82%,#e4622a 100%)}
.hero h1{position:absolute;left:0;right:0;top:100px;text-align:center;color:#fff;font-weight:400;font-size:24px;line-height:29px}
.hero-arrow{position:absolute;top:126px;width:25px;height:25px}

/* intro */
.intro-title{left:0;width:746px;top:409px;text-align:center;font-size:15px;font-weight:400;color:#333}
.intro-text{left:0;width:746px;top:439px;text-align:center;font-size:7.2px;line-height:12px;color:var(--muted)}
.tile{top:473px;width:80px;height:64px;color:#fff;text-align:center}
.tile svg{display:block;margin:9px auto 0}
.tile span{position:absolute;left:0;right:0;bottom:8px;font-size:6.5px}

/* features */
.features{left:0;top:567px;width:746px;height:329px;background:var(--panel);border-top:1px solid var(--line)}
.feature{position:absolute;width:230px}
.feature svg{position:absolute;left:0;top:0}
.feature h3{position:absolute;left:40px;top:2px;font-size:10.5px;font-weight:400;color:#333;white-space:nowrap}
.feature p{position:absolute;left:42px;top:20px;width:210px;font-size:6.2px;line-height:9px;color:var(--muted)}
.feature a{position:absolute;left:41px;top:45px;font-size:6.8px;color:#444;text-decoration:none;white-space:nowrap}
.feature-divider{left:374px;top:97px;width:1px;height:136px;background:#e0e0e0}

/* quote */
.quote{left:0;top:896px;width:746px;height:218px;
  background:radial-gradient(ellipse at 80% 90%,#3a2a7a,transparent 55%),linear-gradient(180deg,#1d1f6e,#23257a 60%,#2a2466)}
.quote h2{position:absolute;left:0;right:0;top:16px;text-align:center;color:#fff;font-weight:400;font-size:14px}
.quote p{position:absolute;left:0;right:0;top:47px;text-align:center;color:#e8e8f4;font-size:7.2px;line-height:11.5px}
.field{position:absolute;background:#fff;border-radius:1px;font-size:7px;color:#444;padding:7px 6px}
.submit{position:absolute;left:298px;top:164px;width:150px;height:25px;line-height:25px;text-align:center;color:#fff;font-size:7px;font-weight:700;
  background:linear-gradient(90deg,#9b5cf0,#e05a9a 60%,#f2454d)}

/* footer */
.footer-links{left:0;width:746px;text-align:center;font-size:6.2px;color:#777}
.footer-links span{margin:0 5px;color:#999}
.footer-rule{left:0;top:1158px;width:746px;height:1px;background:var(--line)}
.social{top:1168px;width:20px;height:20px;border-radius:50%;background:var(--navy)}
.copyright{left:420px;top:1174px;font-size:6.2px;color:#777}
.copyright b{color:var(--navy);font-weight:500}
</style>
</head>
<body>

<!-- header -->
<div class="abs brand"><div class="brand-dot"></div><div class="brand-name">Inkvale</div></div>
<div class="abs tagline"><strong>“Every page, done with care”</strong><span>Professional photocopying - digital &amp; film processing, design and printing</span></div>
<div class="abs contact"><strong>• 07 555 0147,</strong>• 7/58 Harbour Lane - Westbay - Kowhai</div>

<nav class="abs util-bar">
  <a style="left:24px">Passport Photos</a><i class="sep" style="left:94px"></i>
  <a style="left:110px">Image Restoration</a><i class="sep" style="left:190px"></i>
  <a style="left:204px">Printer Supplies</a><i class="sep" style="left:274px"></i>
  <a style="left:286px">Free Quote</a><i class="sep" style="left:341px"></i>
  <a style="left:354px">Contact</a>
</nav>

<nav class="abs main-nav">
  <a class="active" style="left:100px">Home</a>
  <a style="left:148px">About</a><i class="sep" style="left:180px"></i>
  <a style="left:188px">Photocopying</a><i class="sep" style="left:248px"></i>
  <a style="left:257px">Printing</a><i class="sep" style="left:293px"></i>
  <a style="left:304px">Laminating</a><i class="sep" style="left:352px"></i>
  <a style="left:362px">Business Cards</a><i class="sep" style="left:422px"></i>
  <a style="left:432px">Typing Services</a><i class="sep" style="left:495px"></i>
  <a style="left:505px">Film Processing</a><i class="sep" style="left:570px"></i>
  <a style="left:581px">Photo Printing</a><i class="sep" style="left:642px"></i>
</nav>

<!-- hero -->
<section class="abs hero" role="img" aria-label="Hand reaching toward floating photo prints over a colourful gradient with a hot air balloon">
  <h1>Digital Printing, Laminating &amp; Photocopying<br>Services Throughout Kowhai</h1>
  <svg class="hero-arrow" style="left:14px" viewBox="0 0 26 26"><circle cx="13" cy="13" r="11.5" fill="none" stroke="#fff" stroke-width="2"/><path d="M18 13H8M12 9l-4 4 4 4" fill="none" stroke="#fff" stroke-width="2.2" stroke-linecap="round" stroke-linejoin="round"/></svg>
  <svg class="hero-arrow" style="left:707px" viewBox="0 0 26 26"><circle cx="13" cy="13" r="11.5" fill="none" stroke="#fff" stroke-width="2"/><path d="M8 13h10M14 9l4 4-4 4" fill="none" stroke="#fff" stroke-width="2.2" stroke-linecap="round" stroke-linejoin="round"/></svg>
</section>

<!-- intro -->
<h2 class="abs intro-title">Lorem ipsum dolor sit amet, consectetuer adipiscing</h2>
<p class="abs intro-text">liquam erat volutpat. Ut wisi enim ad minim veniam, quis nostrud exerci tation ullamcorper<br>suscipit lobortis nisl ut aliquip ex ea commodo consequat.</p>

<div class="abs tile" style="left:100px;background:var(--blue)">
  <svg width="44" height="34" viewBox="0 0 44 34" fill="none" stroke="#fff" stroke-width="2.4" stroke-linejoin="round"><path d="M22 2 40 10 22 18 4 10Z"/><path d="M4 16l18 8 18-8M4 22l18 8 18-8"/></svg><span>Photocopying</span></div>
<div class="abs tile" style="left:193px;background:var(--pink)">
  <svg width="40" height="34" viewBox="0 0 40 34" fill="none" stroke="#fff" stroke-width="2.4"><rect x="3" y="5" width="34" height="27"/><path d="M7 1v7M13 1v7M19 1v7M25 1v7M31 1v7M9 15h22M9 21h22M9 27h22"/></svg><span>Laminating &amp; Binding</span></div>
<div class="abs tile" style="left:286px;background:var(--red)">
  <svg width="40" height="34" viewBox="0 0 40 34" fill="#fff"><rect x="10" y="1" width="16" height="12"/><rect x="2" y="13" width="36" height="13" rx="2"/><rect x="9" y="22" width="22" height="11" fill="var(--red)" stroke="#fff" stroke-width="2.4"/></svg><span>Digital Printing</span></div>
<div class="abs tile" style="left:378px;background:var(--plum)">
  <svg width="38" height="34" viewBox="0 0 38 34"><circle cx="17" cy="17" r="15" fill="#fff"/><g fill="var(--plum)"><circle cx="17" cy="8" r="4"/><circle cx="8" cy="17" r="4"/><circle cx="26" cy="17" r="4"/><circle cx="17" cy="26" r="4"/></g><path d="M25 31h12" stroke="#fff" stroke-width="2.4"/></svg><span>Film Processing</span></div>
<div class="abs tile" style="left:471px;background:var(--yellow)">
  <svg width="40" height="34" viewBox="0 0 40 34" fill="none" stroke="#fff" stroke-width="2.4"><path d="M6 10 26 3l3 7"/><rect x="4" y="10" width="32" height="22" rx="2" fill="#fff"/><rect x="24" y="17" width="12" height="8" fill="var(--yellow)" stroke="#fff"/></svg><span>Business Cards</span></div>
<div class="abs tile" style="left:565px;background:var(--green)">
  <svg width="40" height="34" viewBox="0 0 40 34" fill="#fff"><rect x="10" y="1" width="20" height="9"/><rect x="2" y="12" width="36" height="13" rx="3"/><rect x="10" y="22" width="20" height="11" fill="var(--green)" stroke="#fff" stroke-width="2.4"/></svg><span>Photo Printing</span></div>

<!-- features -->
<section class="abs features">
  <div class="feature" style="left:100px;top:30px">
    <svg width="30" height="30" viewBox="0 0 30 30" fill="var(--navy)"><ellipse cx="15" cy="18" rx="13" ry="10"/><circle cx="21" cy="6" r="4"/><rect x="7" y="24" width="4" height="6"/><rect x="18" y="24" width="4" height="6"/></svg>
    <h3>Cost effective Photocopying</h3>
    <p>No matter the quantity of photocopies you need or the size of your copy - you can rely on us to provide a top quality service!</p>
    <a>Click for Photocopying</a>
  </div>
  <div class="feature" style="left:402px;top:30px">
    <svg width="30" height="30" viewBox="0 0 30 30" fill="none" stroke="var(--navy)" stroke-width="2.6"><rect x="2" y="4" width="26" height="17" rx="1"/><path d="M15 21v5M9 27h12"/></svg>
    <h3>Personal desktop publishing</h3>
    <p>From personalised brochures, posters and birthday and special occasion cards to top quality, cheap business cards - you get it all</p>
    <a>Click for Desktop Publishing</a>
  </div>
  <div class="feature" style="left:100px;top:132px">
    <svg width="30" height="30" viewBox="0 0 30 30"><rect x="1" y="7" width="28" height="20" rx="3" fill="var(--navy)"/><rect x="4" y="4" width="7" height="4" fill="var(--navy)"/><circle cx="15" cy="17" r="6.5" fill="none" stroke="#fff" stroke-width="2"/></svg>
    <h3>All digital format printing</h3>
    <p>Either email us your file or bring it into the store and we can get you the print youneed. All prints are to the highest quality</p>
    <a>Click for Digital Printing</a>
  </div>
  <div class="feature" style="left:402px;top:132px">
    <svg width="32" height="30" viewBox="0 0 32 30" fill="var(--navy)"><circle cx="7" cy="7" r="5.5"/><circle cx="18" cy="7" r="5.5"/><rect x="2" y="13" width="22" height="15" rx="2"/><path d="M24 17l7-4v15l-7-4z"/><circle cx="7" cy="7" r="2.5" fill="#f4f4f6"/><circle cx="18" cy="7" r="2.5" fill="#f4f4f6"/></svg>
    <h3>Film photo processing</h3>
    <p>Bring in your film to the store and we will work with you to get the best quality print for your purpose and needs. We work with it all</p>
    <a>Click for Photo Film Processing</a>
  </div>
  <div class="feature" style="left:100px;top:230px">
    <svg width="30" height="40" viewBox="0 0 30 40" fill="none" stroke="var(--navy)" stroke-width="2.6"><rect x="2" y="5" width="26" height="33" rx="1"/><path d="M8 1v7M15 1v7M22 1v7M8 17h14M8 24h14M8 31h14"/></svg>
    <h3>Laminating and binding</h3>
    <p>Create a professional image for your documents or books. Lamination and binding also keeps your documents well protected!</p>
    <a>Click for Lamination &amp; Binding</a>
  </div>
  <div class="feature" style="left:402px;top:230px">
    <svg width="34" height="40" viewBox="0 0 34 40"><rect x="2" y="2" width="20" height="34" rx="3" fill="none" stroke="var(--navy)" stroke-width="2.6"/><rect x="7" y="10" width="3" height="16" fill="var(--navy)"/><circle cx="24" cy="29" r="8" fill="var(--navy)"/><circle cx="24" cy="29" r="3" fill="#f4f4f6"/></svg>
    <h3>Quality digital photo prints</h3>
    <p>Get your photo printed to your requirements - either from a file or from your digital camera.With a wide range of options you..</p>
    <a>Digital Photo Printing</a>
  </div>
  <div class="abs feature-divider"></div>
</section>

<!-- quote -->
<section class="abs quote">
  <h2>Get a free quote</h2>
  <p>...or talk to our team about your requirements. Please fillout the form below and we will contact you within a day.<br>You can now upload and send us your file for a free quote!</p>
  <div class="field" style="left:100px;top:90px;width:154px;height:22px">First name</div>
  <div class="field" style="left:263px;top:90px;width:155px;height:22px">Last name:</div>
  <div class="field" style="left:100px;top:122px;width:154px;height:22px">Email:</div>
  <div class="field" style="left:263px;top:122px;width:155px;height:22px">Last name:</div>
  <div class="field" style="left:424px;top:90px;width:221px;height:54px">Message:</div>
  <div class="submit">SUBMIT MESSAGE</div>
</section>

<!-- footer -->
<nav class="abs footer-links" style="top:1127px">HOME<span>|</span>ABOUT<span>|</span>PHOTOCOPYING<span>|</span>PRINTING<span>|</span>LAMINATING<span>|</span>BUSINESS CARDS<span>|</span>TYPING SERVICES<span>|</span>FILM PROCESSING</nav>
<nav class="abs footer-links" style="top:1141px">PHOTO PRINTING<span>|</span>PASSPORT PHOTOS<span>|</span>IMAGE RESTORATION<span>|</span>PRINTER SUPPLIES<span>|</span>FREE QUOTE<span>|</span>CONTACT</nav>
<div class="abs footer-rule"></div>
<div class="abs social" style="left:101px"></div>
<div class="abs social" style="left:123px"></div>
<div class="abs social" style="left:145px"></div>
<div class="abs social" style="left:168px"></div>
<div class="abs social" style="left:190px"></div>
<div class="abs copyright">© 2015 <b>Inkvale</b>. All Rights Reserved. Privacy Policy and Tems &amp; Conditions</div>

</body>
</html>
```